Meridale Real Estate

We are looking for help with web design for a new company that is revolutionizing the real estate world on the listing side: by charing per hour for top level professional real estate services. We would like the concept to be simple, clean and easily understood.
Updates

We want this website to actually function, not just a static design.

Industry/Entity Type

Real Estate

```html
<!DOCTYPE html>
<html lang="en">
<head>
<meta charset="utf-8">
<title>Meridale Real Estate — Property Search</title>
<link href="https://fonts.googleapis.com/css2?family=Roboto+Condensed:wght@400;700&family=Open+Sans:wght@400;600;700&display=swap" rel="stylesheet">
<style>
:root{
  --ink:#2b2d33;
  --text:#4a4d55;
  --muted:#7b7f88;
  --blue:#2ca6de;
  --blue-light:#4fbbe9;
  --blue-dark:#1c8fc6;
  --navy:#232427;
  --slate:#3b3d45;
  --slate-line:#55575f;
  --band:#3a3b43;
  --band-line:#2f3037;
  --field:#ffffff;
  --field-line:#c9d3db;
  --sky-top:#f6fafd;
  --sky-bottom:#dde9f2;
  --city:#c3d6e6;
  --red:#e4141b;
  --star:#f5a31a;
  --star-off:#d3d3d3;
  --rule:#e4e6e9;
}
*{box-sizing:border-box;margin:0;padding:0}
html,body{width:1040px;height:1200px;overflow:hidden;background:#fff}
body{position:relative;font-family:"Open Sans",Arial,sans-serif;color:var(--text);font-size:12px}
.abs{position:absolute}

/* top navigation */
.topbar{position:absolute;left:0;top:0;width:1040px;height:48px;background:var(--navy)}
.topnav a{position:absolute;top:17px;color:#fff;text-decoration:none;font-family:"Roboto Condensed",sans-serif;font-size:13px;letter-spacing:.2px}
.account-btn{position:absolute;top:0;height:48px;color:#fff;display:flex;align-items:center;gap:8px;padding-left:12px;text-decoration:none}
.account-btn small{display:block;font-size:9px;line-height:10px}
.account-btn strong{display:block;font-family:"Roboto Condensed",sans-serif;font-weight:400;font-size:16px;line-height:17px}
.btn-create{left:722px;width:101px;background:var(--blue-light)}
.btn-login{left:823px;width:103px;background:var(--blue)}

/* hero search */
.hero{position:absolute;left:0;top:48px;width:1040px;height:593px;background:linear-gradient(var(--sky-top),var(--sky-bottom))}
.skyline{position:absolute;left:0;top:480px;width:1040px;height:161px;background:linear-gradient(180deg,rgba(195,214,230,0) 0%,rgba(195,214,230,.75) 55%,var(--city) 100%)}
.brand{position:absolute;left:130px;top:76px;width:100px;text-align:center}
.brand-ring{width:48px;height:48px;border:2px solid var(--ink);border-radius:50%;margin:0 auto 6px}
.brand-name{font-family:"Open Sans",sans-serif;font-weight:600;font-size:11px;letter-spacing:1.5px;text-transform:uppercase;color:var(--ink);line-height:14px}
.page-title{position:absolute;left:0;width:1040px;top:76px;text-align:center;font-family:"Roboto Condensed",sans-serif;font-weight:700;font-size:19px;color:var(--slate);letter-spacing:.3px}
.tab{position:absolute;top:126px;width:112px;height:32px;background:var(--slate);border:1px solid var(--slate-line);color:#fff;font-family:"Roboto Condensed",sans-serif;font-size:13px;display:flex;align-items:center;justify-content:center}
.tab.active{background:var(--blue);border-color:var(--blue)}
.tab.active::after{content:"";position:absolute;left:50%;bottom:-7px;margin-left:-7px;border:7px solid transparent;border-bottom:0;border-top-color:var(--blue)}

.step{position:absolute;display:flex;align-items:center;gap:10px;font-family:"Roboto Condensed",sans-serif;font-size:18px;color:var(--ink)}
.step-num{width:27px;height:27px;border-radius:50%;background:var(--blue-light);color:#fff;font-size:16px;display:flex;align-items:center;justify-content:center}

.chip{position:absolute;width:104px;height:25px;background:var(--slate);color:#fff;font-family:"Open Sans",sans-serif;font-weight:600;font-size:12px;display:flex;align-items:center;justify-content:center}
.chip.active{background:var(--blue)}

.label{position:absolute;font-size:11.5px;color:var(--ink)}
.hint{position:absolute;font-size:11px;color:var(--text);line-height:15px}
.hint-title{position:absolute;font-size:11.5px;font-weight:600;color:var(--ink)}
.field,.select{position:absolute;height:28px;background:var(--field);border:1px solid var(--field-line);border-radius:2px;font-size:11px;color:var(--muted);display:flex;align-items:center;padding-left:8px}
.select::after{content:"";position:absolute;right:9px;top:12px;border:4px solid transparent;border-bottom:0;border-top-color:#555}
.btn-search{position:absolute;height:30px;background:var(--blue);color:#fff;font-family:"Open Sans",sans-serif;font-weight:600;font-size:12px;display:flex;align-items:center;justify-content:center;gap:6px;border-bottom:2px solid var(--blue-dark)}
.btn-search svg{width:13px;height:13px}

/* alternate searches */
.alt-band{position:absolute;left:0;top:641px;width:1040px;height:210px;background:var(--band)}
.alt-divider{position:absolute;left:520px;top:641px;width:1px;height:210px;background:var(--band-line)}
.or-badge{position:absolute;left:504px;top:626px;width:32px;height:32px;border-radius:50%;background:var(--blue);border:2px solid #fff;color:#fff;font-size:11px;font-weight:700;display:flex;align-items:center;justify-content:center}
.alt-title{position:absolute;top:670px;font-family:"Open Sans",sans-serif;font-weight:700;font-size:17px;color:#fff}
.alt-note{position:absolute;top:746px;left:588px;font-size:11px;color:#a6a8ae}

/* featured listings */
.section-rule{position:absolute;top:889px;height:1px;background:var(--rule)}
.section-title{position:absolute;top:878px;left:0;width:1040px;text-align:center;font-family:"Roboto Condensed",sans-serif;font-weight:700;font-size:17px;color:var(--slate);letter-spacing:.3px}
.card{position:absolute;top:929px;width:175px}
.card-photo{width:175px;height:117px;border:1px solid var(--rule);padding:4px;background:#fff}
.card-photo div{width:100%;height:100%}
.tag{position:absolute;right:2px;top:2px;background:var(--red);color:#fff;font-size:9px;padding:3px 8px}
.card-name{margin-top:11px;font-weight:600;font-size:12.5px;color:var(--ink)}
.card-loc{font-size:11px;color:var(--muted);margin-top:2px}
.stars{font-size:14px;color:var(--star);letter-spacing:1px;margin-top:1px}
.stars .off{color:var(--star-off)}
.carousel-arrow{position:absolute;top:975px;width:14px;height:28px}

/* footer */
.footer-rule{position:absolute;left:0;top:1143px;width:1040px;height:1px;background:var(--rule)}
.copyright{position:absolute;left:113px;top:1164px;font-size:9px;font-weight:700;color:var(--ink)}
.social{position:absolute;top:1158px;width:22px;height:22px}
</style>
</head>
<body>

<header class="topbar">
  <nav class="topnav">
    <a style="left:381px">HOME</a>
    <a style="left:446px">ABOUT US</a>
    <a style="left:529px">SERVICES</a>
    <a style="left:611px">CONTACT US</a>
  </nav>
  <a class="account-btn btn-create">
    <svg width="16" height="18" viewBox="0 0 16 18"><circle cx="8" cy="5" r="4" fill="#fff"/><path d="M0 18c0-5 3.5-7.5 8-7.5s8 2.5 8 7.5z" fill="#fff"/></svg>
    <span><small>Create an</small><strong>Account</strong></span>
  </a>
  <a class="account-btn btn-login">
    <svg width="16" height="19" viewBox="0 0 16 19"><path d="M3.5 8V5.5a4.5 4.5 0 0 1 9 0V8" fill="none" stroke="#fff" stroke-width="2.2"/><rect x="0" y="8" width="16" height="11" rx="1.5" fill="#fff"/></svg>
    <span><small>Customer</small><strong>Login</strong></span>
  </a>
</header>

<section class="hero">
  <div class="skyline" role="img" aria-label="Soft blue city skyline illustration with rolling hills"></div>
</section>

<div class="brand">
  <div class="brand-ring"></div>
  <div class="brand-name">Meridale<br>Real Estate</div>
</div>

<h1 class="page-title">PROPERTY SEARCH</h1>
<div class="tab" style="left:291px">COMMERCIAL</div>
<div class="tab active" style="left:407px">RESIDENTIAL</div>
<div class="tab" style="left:522px">FARM</div>
<div class="tab" style="left:638px">VACANT LAND</div>

<!-- step 1 -->
<div class="step" style="left:114px;top:179px"><span class="step-num">1</span>Search Properties for Sale by</div>
<div class="chip active" style="left:114px;top:223px">City</div>
<div class="chip" style="left:224px;top:223px">Country</div>
<div class="chip" style="left:114px;top:254px">Zip Code</div>
<div class="chip" style="left:224px;top:254px">Neighborhood</div>

<!-- step 2 -->
<div class="step" style="left:452px;top:179px"><span class="step-num">2</span>Type Location to Center on</div>
<div class="hint" style="left:452px;top:219px">Radius defines the size of a circle centered on this address.</div>
<div class="field" style="left:452px;top:250px;width:235px">Street Address</div>
<div class="field" style="left:696px;top:250px;width:122px">City</div>
<div class="select" style="left:827px;top:250px;width:99px">Radius</div>

<!-- step 3 -->
<div class="step" style="left:114px;top:323px"><span class="step-num">3</span>Choose Your Options</div>
<div class="label" style="left:114px;top:366px">Price Range</div>
<div class="field" style="left:114px;top:386px;width:127px">Min.</div>
<div class="label" style="left:254px;top:393px">to</div>
<div class="field" style="left:275px;top:386px;width:128px">Max.</div>

<div class="label" style="left:114px;top:428px">Bedrooms</div>
<div class="label" style="left:213px;top:428px">Bedrooms</div>
<div class="label" style="left:313px;top:428px">Pool</div>
<div class="select" style="left:114px;top:448px;width:90px">Any</div>
<div class="select" style="left:213px;top:448px;width:90px">Any</div>
<div class="select" style="left:313px;top:448px;width:90px">Any</div>

<div class="label" style="left:114px;top:491px">Square Footage</div>
<div class="label" style="left:213px;top:491px">Age of Home</div>
<div class="label" style="left:313px;top:491px">Stories</div>
<div class="select" style="left:114px;top:511px;width:90px">Any</div>
<div class="select" style="left:213px;top:511px;width:90px">Any</div>
<div class="select" style="left:313px;top:511px;width:90px">Any</div>

<div class="label" style="left:114px;top:553px">Min. Acreage</div>
<div class="select" style="left:114px;top:574px;width:90px">Any</div>

<!-- step 4 -->
<div class="step" style="left:452px;top:323px"><span class="step-num">4</span>Advanced Options</div>
<div class="label" style="left:452px;top:366px">Show Foreclosed</div>
<div class="select" style="left:452px;top:386px;width:135px">Yes</div>
<div class="label" style="left:452px;top:428px">Show Short Sales</div>
<div class="select" style="left:452px;top:448px;width:135px">Yes - All</div>
<div class="label" style="left:452px;top:491px">Show Pendings?</div>
<div class="select" style="left:452px;top:511px;width:135px">Where Available</div>
<div class="btn-search" style="left:452px;top:557px;width:97px">
  <svg viewBox="0 0 13 13"><circle cx="5.3" cy="5.3" r="4" fill="none" stroke="#fff" stroke-width="1.8"/><path d="M8.3 8.3l3.7 3.7" stroke="#fff" stroke-width="2"/></svg>SEARCH</div>

<div class="hint-title" style="left:612px;top:366px">What is Foreclosed?</div>
<div class="hint" style="left:612px;top:385px;width:320px">Properties in the possession of a lender as a result of foreclosure or forfeiture.</div>
<div class="hint-title" style="left:612px;top:428px">What is Short Sale?</div>
<div class="hint" style="left:612px;top:448px;width:325px">The result of the current lender considering to offer the property for sale at less than the outstanding amount owed.</div>

<!-- alternate searches -->
<section class="alt-band"></section>
<div class="alt-divider"></div>
<div class="or-badge">OR</div>

<h2 class="alt-title" style="left:114px">ADDRESS SEARCH</h2>
<div class="field" style="left:114px;top:704px;width:338px">Address Search</div>
<div class="field" style="left:114px;top:746px;width:107px">Street Number</div>
<div class="field" style="left:231px;top:746px;width:104px">Street Name</div>
<div class="field" style="left:348px;top:746px;width:104px">City</div>
<div class="btn-search" style="left:114px;top:787px;width:97px">
  <svg viewBox="0 0 13 13"><circle cx="5.3" cy="5.3" r="4" fill="none" stroke="#fff" stroke-width="1.8"/><path d="M8.3 8.3l3.7 3.7" stroke="#fff" stroke-width="2"/></svg>SEARCH</div>

<h2 class="alt-title" style="left:588px">MLS SEARCH</h2>
<div class="field" style="left:588px;top:704px;width:338px">MLS Number</div>
<div class="alt-note">Searches through all property types</div>
<div class="btn-search" style="left:588px;top:787px;width:97px">
  <svg viewBox="0 0 13 13"><circle cx="5.3" cy="5.3" r="4" fill="none" stroke="#fff" stroke-width="1.8"/><path d="M8.3 8.3l3.7 3.7" stroke="#fff" stroke-width="2"/></svg>SEARCH</div>

<!-- featured listings -->
<div class="section-rule" style="left:114px;width:320px"></div>
<div class="section-rule" style="left:606px;width:320px"></div>
<h2 class="section-title">HOT PROPERTY</h2>

<svg class="carousel-arrow" style="left:112px" viewBox="0 0 14 28"><path d="M12 2L3 14l9 12" fill="none" stroke="#c4c7cc" stroke-width="2"/></svg>
<svg class="carousel-arrow" style="left:913px" viewBox="0 0 14 28"><path d="M2 2l9 12-9 12" fill="none" stroke="#c4c7cc" stroke-width="2"/></svg>

<article class="card" style="left:139px">
  <div class="card-photo"><div role="img" aria-label="Glass office building at dusk" style="background:linear-gradient(180deg,#8fb0d4 0%,#4d6f96 60%,#5b6a72 100%)"></div></div>
  <span class="tag">For Sale</span>
  <div class="card-name">Linden Park Avenue</div>
  <div class="card-loc">Las Vegas, NV</div>
  <div class="stars">★★★★<span class="off">★</span></div>
</article>
<article class="card" style="left:334px">
  <div class="card-photo"><div role="img" aria-label="Brick family house with green lawn" style="background:linear-gradient(180deg,#a9c6e4 0%,#9a6e58 45%,#5f8c3e 100%)"></div></div>
  <span class="tag">For Sale</span>
  <div class="card-name">Hollis Bungalows</div>
  <div class="card-loc">Las Vegas, NV</div>
  <div class="stars">★★★★★</div>
</article>
<article class="card" style="left:529px">
  <div class="card-photo"><div role="img" aria-label="Farm with red barn and silos under blue sky" style="background:linear-gradient(180deg,#5f96cc 0%,#a7c3da 45%,#7e9a52 75%,#5d7d38 100%)"></div></div>
  <span class="tag">For Sale</span>
  <div class="card-name">Brookside Farm</div>
  <div class="card-loc">Las Vegas, NV</div>
  <div class="stars">★★★★<span class="off">★</span></div>
</article>
<article class="card" style="left:724px">
  <div class="card-photo"><div role="img" aria-label="Cleared plot of vacant land edged by trees" style="background:linear-gradient(180deg,#6f8a4a 0%,#8d8a5c 40%,#c9a37a 70%,#b98e65 100%)"></div></div>
  <span class="tag">For Sale</span>
  <div class="card-name">Westfield Land</div>
  <div class="card-loc">Las Vegas, NV</div>
  <div class="stars">★★★★★</div>
</article>

<!-- footer -->
<div class="footer-rule"></div>
<p class="copyright">Copyrights 2015 Meridale Real Estate. All Right Reserved</p>
<div class="social" style="left:855px;background:#3b5a9a" role="img" aria-label="Social profile link"></div>
<div class="social" style="left:879px;background:#2aa3e0" role="img" aria-label="Social profile link"></div>
<div class="social" style="left:904px;background:#1b74b3" role="img" aria-label="Social profile link"></div>

</body>
</html>
```